KPV Datacore Solutions

We need a Logo and Website for our company based in London. We are a IT recruitment company . We provide quality resources to top IT company across UK.

Industry/Entity Type

It Company

Number of Pages Required

4 page

```html
<!DOCTYPE html>
<html lang="en">
<head>
<meta charset="utf-8">
<title>KPV Datacore Solutions</title>
<link href="https://fonts.googleapis.com/css2?family=Lato:wght@400;700;900&family=Open+Sans:wght@600;700;800&display=swap" rel="stylesheet">
<style>
:root{
  --navy:#0e2a43;
  --navy-deep:#0b2236;
  --blue:#1a8fd0;
  --blue-light:#2aa8e4;
  --blue-dark:#0f6aa6;
  --heading:#1c6fa8;
  --text:#3a3a3a;
  --white:#ffffff;
  --strip:#1673a9;
}
*{margin:0;padding:0;box-sizing:border-box}
html,body{width:798px;height:1200px;overflow:hidden;background:#fff}
body{position:relative;font-family:'Lato',sans-serif;color:var(--text)}
.abs{position:absolute}
/* header */
.site-header{left:0;top:0;width:798px;height:64px;background:var(--navy)}
.brand{left:78px;top:18px;font-family:'Open Sans',sans-serif;font-weight:800;font-size:16px;color:var(--white);letter-spacing:.2px}
.brand span{font-weight:600;color:var(--blue-light)}
.main-nav a{position:absolute;top:28px;font-size:10px;color:var(--white);text-decoration:none}
.nav-active{left:400px;top:62px;width:32px;height:2px;background:var(--white)}
/* hero */
.hero{left:0;top:64px;width:798px;height:252px;background:linear-gradient(180deg,#1f9ad8,#0f7fc0)}
.hero-photo{left:72px;top:96px;width:330px;height:220px;background:linear-gradient(180deg,#3e86b6,#27364a);border-radius:90px 90px 0 0}
.hero-title{left:420px;top:152px;width:300px;text-align:center;font-family:'Open Sans',sans-serif;font-weight:800;font-size:19px;color:var(--white)}
.hero-text{left:430px;top:181px;width:280px;text-align:center;font-size:11px;line-height:17px;color:#e4f3fb}
.btn-dark{left:512px;top:226px;width:104px;height:25px;background:var(--navy);color:var(--white);font-size:8px;font-weight:700;text-align:center;line-height:25px;letter-spacing:.3px}
.dots{left:700px;top:302px;display:flex;gap:3px}
.dots i{width:4px;height:4px;border-radius:50%;background:#fff}
/* steps */
.step{top:337px;width:191px;height:123px;background:linear-gradient(180deg,#28a6e2,#1485c6);color:var(--white);font-size:10px;font-weight:700;line-height:17px;padding:58px 16px 0}
.step-icon{position:absolute;left:9px;top:14px;width:38px;height:38px;border-radius:50%;background:rgba(255,255,255,.2)}
/* sections */
.sec-title{font-size:15px;font-weight:700;color:var(--heading)}
.feature-icon{width:32px;height:32px;border-radius:50%;background:#1b4f80}
.feature-title{width:145px;font-size:9.5px;color:var(--heading);line-height:13px;letter-spacing:.2px}
.feature-text{width:143px;font-size:8px;line-height:14px;text-align:justify}
.rule{height:1px;background:#e3e3e3}
.divider{left:289px;top:520px;width:1px;height:280px;background:#e3e3e3}
.team-photo{top:520px;width:190px;height:123px}
.help-title{top:655px;font-size:11.5px;font-weight:700;color:var(--heading)}
.checklist{list-style:none;font-size:8.5px;color:#555}
.checklist li{height:19px;display:flex;align-items:center;gap:8px}
.checklist li::before{content:"";width:7px;height:7px;background:#1c6fa8;border-radius:1px}
.btn-blue{top:761px;width:163px;height:29px;background:#1c94d4;color:var(--white);font-size:7.5px;font-weight:700;line-height:29px;padding-left:24px}
.btn-blue::before{content:"";position:absolute;left:11px;top:11px;width:8px;height:7px;background:#fff;border-radius:3px 3px 1px 1px}
/* blue band */
.band{left:0;top:812px;width:798px;height:280px;background:linear-gradient(180deg,#137cbd,#1a93d3 60%,#1586c6)}
.band-title{font-size:15px;color:var(--white)}
.map{left:99px;top:861px;width:218px;height:103px;background:linear-gradient(135deg,#dfe6ea,#b9d8ec);border:4px solid #7fb9df}
.address{left:110px;top:978px;font-size:8px;font-weight:700;color:var(--white);line-height:17px}
.pin{left:99px;top:980px}
.client{width:152px;height:94px;background:linear-gradient(180deg,#1a6fb0,#0f5d98);color:var(--white);font-size:17px;font-weight:700;display:flex;align-items:center;justify-content:center}
.arrow-btn{top:830px;width:14px;height:13px;background:var(--navy)}
/* social strip */
.social{left:0;top:1092px;width:798px;height:64px;background:var(--strip)}
.social-item{top:1110px;display:flex;align-items:center;gap:9px;font-size:8px;color:var(--white);line-height:10px}
.social-item i{width:21px;height:21px;border:1.5px solid #fff;border-radius:50%}
/* footer */
.site-footer{left:0;top:1156px;width:798px;height:44px;background:var(--navy-deep)}
.foot-nav a{position:absolute;top:1174px;font-size:7px;color:var(--white);text-decoration:none}
.copyright{left:600px;top:1174px;font-size:6.5px;color:var(--white)}
.mark{left:744px;top:1174px;font-size:6.5px;color:var(--white)}
</style>
</head>
<body>
<header class="abs site-header"></header>
<div class="abs brand">KPV DATACORE <span>SOLUTIONS</span></div>
<nav class="main-nav">
  <a style="left:404px">HOME</a><a style="left:459px">ABOUT</a><a style="left:519px">EMPLOYERS</a><a style="left:599px">JOBSEEKERS</a><a style="left:682px">CONTACT</a>
</nav>
<div class="abs nav-active"></div>

<section class="abs hero"></section>
<div class="abs hero-photo" role="img" aria-label="Team of smiling recruitment consultants in business suits"></div>
<h1 class="abs hero-title">KPV Datacore Solutions</h1>
<p class="abs hero-text">Lorem ipsum dolor sit amet conse ctetur adipisicing elit, s labore et dolore magna aliqua.</p>
<div class="abs btn-dark">POST YOUR RESUME</div>
<div class="abs dots"><i></i><i></i><i></i></div>

<div class="abs step" style="left:87px"><span class="step-icon"></span>Submit a job specification then we contact the relevant recruitment agency for you.</div>
<div class="abs step" style="left:305px"><span class="step-icon"></span>There is no haggling on placement fees as you decide what fee you would like to pay.</div>
<div class="abs step" style="left:522px"><span class="step-icon"></span>We email the agency and give your details once they agree to the terms.</div>
<svg class="abs" style="left:250px;top:368px" width="300" height="50" viewBox="0 0 300 50">
  <path d="M6 28 Q40 -2 70 22" fill="none" stroke="#156aa0" stroke-width="3"/>
  <path d="M62 14 L72 24 L60 26 Z" fill="#156aa0"/>
  <path d="M226 24 Q250 46 290 24" fill="none" stroke="#156aa0" stroke-width="3"/>
  <path d="M282 18 L292 22 L284 30 Z" fill="#156aa0"/>
</svg>
<svg class="abs" style="left:106px;top:360px" width="20" height="20" viewBox="0 0 20 20"><rect x="5" y="3" width="10" height="13" fill="none" stroke="#fff" stroke-width="1.4"/><path d="M7 8h6M7 11h6" stroke="#fff"/></svg>
<svg class="abs" style="left:324px;top:360px" width="20" height="20" viewBox="0 0 20 20"><text x="10" y="15" fill="#fff" font-size="14" font-family="Lato,sans-serif" font-weight="700" text-anchor="middle">$</text></svg>
<svg class="abs" style="left:541px;top:360px" width="20" height="20" viewBox="0 0 20 20"><rect x="3" y="5" width="14" height="10" fill="#fff"/><path d="M3 5 L10 11 L17 5" fill="none" stroke="#1a8fd0" stroke-width="1.3"/></svg>

<h2 class="abs sec-title" style="left:89px;top:483px">FEATURES OVERVIEW</h2>
<h2 class="abs sec-title" style="left:306px;top:483px">HOW CAN KPV DATACORE SOLUTIONS HELP YOU?</h2>

<div class="abs feature-icon" style="left:91px;top:520px"></div>
<div class="abs feature-title" style="left:134px;top:525px">COMMODO CONSEQUAT DUIS AUTE IRURE</div>
<p class="abs feature-text" style="left:134px;top:555px">Lorem ipsum dolor sit amet conse ctetur adipisicing elit, s labore et dolore magna aliqua.</p>
<div class="abs rule" style="left:106px;top:602px;width:170px"></div>
<div class="abs feature-icon" style="left:91px;top:618px"></div>
<div class="abs feature-title" style="left:134px;top:623px">COMMODO CONSEQUAT DUIS AUTE IRURE</div>
<p class="abs feature-text" style="left:134px;top:653px">Lorem ipsum dolor sit amet conse ctetur adipisicing elit, s labore et dolore magna aliqua.</p>
<div class="abs rule" style="left:106px;top:698px;width:170px"></div>
<div class="abs feature-icon" style="left:91px;top:710px"></div>
<div class="abs feature-title" style="left:134px;top:715px">COMMODO CONSEQUAT DUIS AUTE IRURE</div>
<p class="abs feature-text" style="left:134px;top:745px">Lorem ipsum dolor sit amet conse ctetur adipisicing elit, s labore et dolore magna aliqua.</p>
<svg class="abs" style="left:91px;top:520px" width="32" height="222" viewBox="0 0 32 222">
  <path d="M10 12h12M10 16h12M10 20h12" stroke="#fff" stroke-width="2"/>
  <circle cx="15" cy="113" r="5" fill="none" stroke="#fff" stroke-width="2"/><path d="M19 117 L23 121" stroke="#fff" stroke-width="2.4"/>
  <rect x="10" y="200" width="11" height="11" fill="#fff"/>
</svg>
<div class="abs divider"></div>

<div class="abs team-photo" style="left:305px;background:linear-gradient(180deg,#c9d7e2,#8aa7bd)" role="img" aria-label="Smiling professional woman in front of colleagues"></div>
<div class="abs team-photo" style="left:521px;background:linear-gradient(180deg,#d7e2ea,#6f8496)" role="img" aria-label="Business people shaking hands in an office"></div>
<div class="abs help-title" style="left:306px">FOR EMPLOYERS</div>
<div class="abs help-title" style="left:521px">FOR JOBSEEKERS</div>
<ul class="abs checklist" style="left:307px;top:677px">
  <li>Find recuitment agencies</li><li>Learn about your industry</li><li>Let us assist you</li><li>Salary surveys</li>
</ul>
<ul class="abs checklist" style="left:523px;top:677px">
  <li>Find recuitment agencies</li><li>Search jobs</li><li>Find your salary</li><li>Direct your career</li>
</ul>
<div class="abs btn-blue" style="left:305px">EMPLOYERS RESOURCES CENTRE</div>
<div class="abs btn-blue" style="left:521px">CANDIDATES RESOURCES CENTRE</div>

<section class="abs band"></section>
<h2 class="abs band-title" style="left:99px;top:832px">CONTACT</h2>
<div class="abs map" role="img" aria-label="Street map of the office location"></div>
<svg class="abs pin" width="8" height="10" viewBox="0 0 8 10"><path d="M4 10 L1 5 A3 3 0 1 1 7 5 Z" fill="#fff"/></svg>
<div class="abs address">12 HARBOUR LANE<br>LONDON<br>E9 2QT</div>
<h2 class="abs band-title" style="left:357px;top:827px">OUR CLIENTS</h2>
<svg class="abs arrow-btn" style="left:659px" viewBox="0 0 14 13"><path d="M8 3 L5 6.5 L8 10" fill="none" stroke="#fff" stroke-width="1.5"/></svg>
<svg class="abs arrow-btn" style="left:676px" viewBox="0 0 14 13"><path d="M6 3 L9 6.5 L6 10" fill="none" stroke="#fff" stroke-width="1.5"/></svg>
<div class="abs client" style="left:357px;top:859px">Northvale</div>
<div class="abs client" style="left:537px;top:859px">Corran &amp; Weald</div>
<div class="abs client" style="left:357px;top:969px">Brightmoor</div>
<div class="abs client" style="left:537px;top:969px">Tessaline</div>

<section class="abs social"></section>
<div class="abs social-item" style="left:92px"><i></i>FOLLOW ME ON<br>QUILLER</div>
<div class="abs social-item" style="left:218px"><i></i>LIKE ME ON<br>FRIENDBOOK</div>
<div class="abs social-item" style="left:327px"><i></i>CONNECT WITH ME<br>SEARCHLY</div>
<div class="abs social-item" style="left:464px"><i></i>CONNECT WITH ME<br>SEARCHLY</div>
<div class="abs social-item" style="left:612px"><i></i>WATCH ME ON<br>VIDZONE</div>

<footer class="abs site-footer"></footer>
<nav class="foot-nav">
  <a style="left:91px">HOME</a><a style="left:133px">ABOUT</a><a style="left:177px">EMPLOYERS</a><a style="left:238px">JOBSEEKERS</a><a style="left:300px">CONTACT</a>
</nav>
<div class="abs copyright">Copyright© 2016. All Rights Reserved.</div>
<div class="abs mark">M1</div>
</body>
</html>
```